Website Design for WestaKolory.pl – Luxury Wedding Car Rental with Chauffeur

We are looking for a talented designer to create a modern, elegant, and fully responsive website for our new brand – WestyKolory.pl. We are a premium car rental platform in Poland, offering luxury and exotic vehicles exclusively for weddings. All cars come with a professional chauffeur, ensuring a high-end, stress-free, and stylish experience.
Website Purpose:
The website should present our offering in a luxurious, clear, and inspiring way. It must build trust, highlight the prestige of our brand, and encourage inquiries. Our target audience includes engaged couples, wedding planners, and clients seeking a truly exceptional vehicle for their special day.
Design Requirements:
Style: modern, elegant, minimalist
Color palette: white, black, gold, optionally silver – refined and luxurious
Typography: clean, modern, high-end
Layout: clear, intuitive, with large car images and well-defined sections
Fully responsive (desktop, tablet, mobile)
Bilingual layout (Polish/English) must be considered
Pages to Design:
Homepage
About Us
Fleet Overview
Individual Car Pages
Services (Weddings, Photo Shoots, Film Rentals)
Why Us / Unique Selling Points
Contact
FAQ
Inspiration:
Luxury automotive brands (e.g. Varnel-Hoske, Corvash, Elbrin Tusko)
High-end wedding websites
Minimalist layouts with large visuals and elegant typography
Additional Notes:
The design should evoke the emotions of a wedding day – elegance, uniqueness, style, and class. Please avoid flashy colors, excessive graphic effects, or overly decorative elements. Subtlety, prestige, and sophistication are key.

```html
<!DOCTYPE html>
<html lang="en">
<head>
<meta charset="utf-8">
<title>WestaKolory.pl – Luxury Wedding Cars</title>
<link href="https://fonts.googleapis.com/css2?family=Inter:ital,wght@0,400;0,500;0,600;0,700;1,400&display=swap" rel="stylesheet">
<style>
:root{
  --gold:#f6d472;
  --gold-soft:#f9e6a8;
  --gold-deep:#d9b24a;
  --navy:#171d2a;
  --navy-card:#252b38;
  --ink:#1c2230;
  --muted:#5b6270;
  --white:#ffffff;
}
*{margin:0;padding:0;box-sizing:border-box}
html,body{width:1200px;height:3082px;overflow:hidden}
body{font-family:"Inter",sans-serif;color:var(--ink);background:var(--white);position:relative}
.wrap{width:696px;margin:0 auto;position:relative}
.gold{color:var(--gold)}
.gold-faint{color:var(--gold-soft)}

/* hero */
.hero{position:relative;height:598px;overflow:hidden;text-align:center;color:var(--white)}
.hero-photo{position:absolute;inset:0;background:radial-gradient(ellipse at 45% 20%,#8a6a35 0%,#4a3b26 35%,#2a2620 70%,#1b1a18 100%)}
.hero-shade{position:absolute;inset:0;background:linear-gradient(180deg,rgba(0,0,0,.15),rgba(0,0,0,.35))}
.hero-inner{position:relative}
.brand{padding-top:54px;font-weight:600;font-size:30px;line-height:36px;color:var(--gold);letter-spacing:1px;display:flex;align-items:center;justify-content:center;gap:10px}
.brand-dot{width:14px;height:14px;border-radius:50%;background:var(--gold)}
.hero h1{margin-top:70px;font-size:58px;font-weight:700;line-height:70px;letter-spacing:-.5px}
.hero p{margin:44px auto 0;width:560px;font-size:15px;line-height:21px;font-weight:400}
.btn{display:inline-block;font-weight:500;border-radius:5px;text-decoration:none}
.btn-gold{background:var(--gold);color:var(--ink);font-size:12px;padding:10px 26px}
.hero .btn-gold{margin-top:30px;width:126px;padding:11px 0}
.mouse{position:absolute;left:591px;top:502px;width:16px;height:24px;border:1.5px solid rgba(255,255,255,.8);border-radius:8px}
.mouse::after{content:"";position:absolute;left:6px;top:5px;width:1.5px;height:6px;background:#fff;border-radius:1px}

/* about */
.about{height:479px;background:linear-gradient(180deg,#fbfbfa,#efedea);text-align:center;padding-top:108px}
h2{font-size:33px;font-weight:600;letter-spacing:-.3px}
.about .lead{margin:24px auto 0;width:570px;font-size:11.5px;line-height:19px;color:var(--muted)}
.features{display:flex;gap:20px;margin-top:40px}
.feature{flex:1;height:169px;background:var(--white);border-radius:8px;box-shadow:0 4px 16px rgba(0,0,0,.07);padding:20px 18px 0}
.icon-circle{width:40px;height:40px;border-radius:50%;background:var(--gold);margin:0 auto;display:flex;align-items:center;justify-content:center}
.feature h3{margin-top:16px;font-size:13px;font-weight:500}
.feature p{margin-top:14px;font-size:10px;line-height:15px;color:var(--muted)}

/* fleet */
.fleet{height:590px;background:var(--navy);color:var(--white);text-align:center;padding-top:62px}
.fleet .sub{margin-top:12px;font-size:12.5px;color:#c9ccd3}
.cars{display:flex;gap:20px;margin-top:44px;text-align:left}
.car{flex:1;height:313px;background:var(--navy-card);border:1px solid #3a4150;border-radius:4px;padding:20px}
.car-photo{height:121px;border-radius:4px;background:linear-gradient(160deg,#4f525a,#2f333c);display:flex;align-items:center;justify-content:center;font-size:8.5px;color:#a8abb2}
.car h3{margin-top:18px;font-size:15px;font-weight:600;line-height:20px}
.car .desc{margin-top:8px;font-size:10px;line-height:15px;color:#c8cbd2}
.car ul{margin-top:10px;list-style:none}
.car li{font-size:8.5px;color:var(--gold);line-height:18px;padding-left:11px;position:relative}
.car li::before{content:"";position:absolute;left:0;top:7px;width:4px;height:4px;border-radius:50%;background:var(--gold)}
.btn-outline{margin-top:31px;background:var(--white);color:var(--ink);border:1.5px solid var(--gold);font-size:9px;padding:7px 20px}

/* details */
.details{height:501px;background:linear-gradient(180deg,#efeeeb,#fbfbfa);padding-top:52px}
.details h2{text-align:center}
.details-grid{display:flex;justify-content:space-between;margin-top:38px}
.points{width:330px;list-style:none}
.points li{position:relative;padding-left:25px;margin-bottom:22px}
.points li svg{position:absolute;left:0;top:0}
.points h4{font-size:12.5px;font-weight:500;line-height:18px}
.points p{margin-top:5px;font-size:9.5px;line-height:16px;color:var(--muted)}
.detail-photo{position:relative;width:327px;height:241px;margin-top:-9px;border-radius:6px;background:linear-gradient(150deg,#d7d6d2,#ece8dc);display:flex;flex-direction:column;align-items:center;justify-content:center;overflow:hidden}
.detail-photo .t1{font-size:11px;color:#77797d}
.detail-photo .t2{margin-top:6px;font-size:8px;color:#8a8c90}
.blob{position:absolute;border-radius:50%;background:rgba(246,212,114,.3)}

/* testimonials */
.reviews{height:344px;background:var(--navy);color:var(--white);text-align:center;padding-top:62px}
.quotes{display:flex;gap:20px;margin-top:36px}
.quote{flex:1;height:154px;background:var(--navy-card);border:1px solid #323948;border-radius:4px;padding:20px 22px 0}
.stars{display:flex;justify-content:center;gap:2px}
.quote p{margin-top:14px;font-size:10.5px;font-style:italic;line-height:18px;color:#cfd2d8}
.quote .who{margin-top:12px;font-size:10px;font-weight:500;color:var(--gold);font-style:normal}

/* cta */
.cta{height:281px;background:linear-gradient(180deg,#1a2030,#141927);color:var(--white);text-align:center;padding-top:60px}
.cta .sub{margin-top:14px;font-size:12.5px;color:#d0d3d9}
.cta .btn-gold{margin-top:22px;padding:11px 25px}
.divider{margin:28px auto 0;width:180px;display:flex;align-items:center;gap:10px}
.divider span{flex:1;height:1px;background:linear-gradient(90deg,transparent,var(--gold-deep))}
.divider span:last-child{background:linear-gradient(90deg,var(--gold-deep),transparent)}
.divider i{width:5px;height:5px;border-radius:50%;background:var(--gold)}

/* footer */
.footer{height:289px;background:var(--navy);color:#c2c5cc;padding-top:40px}
.foot-cols{display:flex}
.foot-brand{width:358px}
.foot-name{display:flex;align-items:center;gap:9px;font-size:15px;font-weight:600;color:var(--white)}
.foot-name i{width:14px;height:14px;border-radius:50%;background:var(--gold)}
.foot-brand p{margin-top:12px;font-size:9.5px;line-height:16px;width:340px}
.socials{display:flex;gap:12px;margin-top:12px}
.socials i{width:13px;height:13px;border-radius:50%;border:1.5px solid var(--gold)}
.foot-col{width:179px}
.foot-col h5{font-size:11px;font-weight:500;color:var(--gold);margin-bottom:10px}
.foot-col ul{list-style:none}
.foot-col li{font-size:9.5px;line-height:20px}
.contact li{display:flex;align-items:center;gap:8px;font-size:8.5px}
.foot-bottom{margin-top:30px;border-top:1px solid #333a48;padding-top:20px;display:flex;justify-content:space-between;font-size:8.5px}
</style>
</head>
<body>

<header class="hero">
  <div class="hero-photo" role="img" aria-label="Bride stepping into a white luxury wedding car as a chauffeur holds the door, in front of a country house at sunset"></div>
  <div class="hero-shade"></div>
  <div class="hero-inner">
    <div class="brand"><span class="brand-dot"></span>WestaKolory</div>
    <h1>An Exceptional Car<br>for Your <span class="gold">Exceptional Day</span></h1>
    <p>Luxury wedding cars with professional chauffeurs. Experience timeless elegance, unmatched comfort, and flawless service on the most important day of your life.</p>
    <a class="btn btn-gold" href="#fleet">View Our Fleet</a>
  </div>
  <div class="mouse"></div>
</header>

<section class="about">
  <div class="wrap">
    <h2>Where Luxury Meets <span class="gold-faint">Love</span></h2>
    <p class="lead">WestaKolory.pl offers a handpicked selection of luxury vehicles exclusively for weddings. Each car comes with a professionally dressed chauffeur, ensuring a seamless, stylish, and stress-free experience. Whether for the ceremony, a photo shoot, or a grand arrival — we deliver elegance that turns heads.</p>
    <div class="features">
      <div class="feature">
        <div class="icon-circle"><svg width="18" height="18" viewBox="0 0 24 24" fill="none" stroke="#1c2230" stroke-width="1.8" stroke-linecap="round"><path d="M3 15v-3l2-4h12l3 4v3z"/><circle cx="7.5" cy="15.5" r="1.8"/><circle cx="16.5" cy="15.5" r="1.8"/></svg></div>
        <h3>Luxury Interiors</h3>
        <p>Premium leather seats, champagne setup, and elegant decorations to make every moment special.</p>
      </div>
      <div class="feature">
        <div class="icon-circle"><svg width="18" height="18" viewBox="0 0 24 24" fill="none" stroke="#1c2230" stroke-width="1.8" stroke-linecap="round"><circle cx="12" cy="8" r="4"/><path d="M5 20c1-4 4-5 7-5s6 1 7 5"/></svg></div>
        <h3>Professional Service</h3>
        <p>Impeccably dressed chauffeurs with white gloves, ensuring punctual and courteous service.</p>
      </div>
      <div class="feature">
        <div class="icon-circle"><svg width="18" height="18" viewBox="0 0 24 24" fill="none" stroke="#1c2230" stroke-width="1.8" stroke-linejoin="round"><path d="M12 20s-8-5-8-11a4 4 0 0 1 8-1 4 4 0 0 1 8 1c0 6-8 11-8 11z"/></svg></div>
        <h3>Unforgettable Moments</h3>
        <p>Creating magical memories for couples with elegant arrivals and perfect photo opportunities.</p>
      </div>
    </div>
  </div>
</section>

<section class="fleet" id="fleet">
  <div class="wrap">
    <h2>Meet Our Signature Wedding Cars</h2>
    <p class="sub">Curated for elegance. Maintained to perfection.</p>
    <div class="cars">
      <article class="car">
        <div class="car-photo" role="img" aria-label="Corvash Aurelle saloon">Car Image Placeholder</div>
        <h3>Corvash Aurelle</h3>
        <p class="desc">The epitome of British luxury and craftsmanship</p>
        <ul><li>Handcrafted interior</li><li>Whisper-quiet ride</li><li>Premium leather</li></ul>
      </article>
      <article class="car">
        <div class="car-photo" role="img" aria-label="Varnel-Hoske Solenne saloon">Car Image Placeholder</div>
        <h3>Varnel-Hoske Solenne</h3>
        <p class="desc">Unparalleled elegance and sophistication</p>
        <ul><li>Starlight headliner</li><li>Magic carpet ride</li><li>Bespoke details</li></ul>
      </article>
      <article class="car">
        <div class="car-photo" role="img" aria-label="Haldor-Wrenn Meridian limousine">Car Image Placeholder</div>
        <h3>Haldor-Wrenn Meridian</h3>
        <p class="desc">German engineering meets ultimate comfort</p>
        <ul><li>Executive seating</li><li>Champagne cooler</li><li>Ambient lighting</li></ul>
      </article>
    </div>
    <a class="btn btn-outline" href="#fleet">Explore the Full Fleet</a>
  </div>
</section>

<section class="details">
  <div class="wrap">
    <h2>Because Every Detail <span class="gold-faint">Matters</span></h2>
    <div class="details-grid">
      <ul class="points">
        <li><svg width="14" height="14" viewBox="0 0 24 24" fill="none" stroke="#f6d472" stroke-width="2"><circle cx="12" cy="12" r="10"/><path d="M7.5 12.5l3 3 6-6"/></svg><h4>Premium vehicles with full decorative setup</h4><p>Every car is meticulously prepared with elegant decorations and luxury amenities</p></li>
        <li><svg width="14" height="14" viewBox="0 0 24 24" fill="none" stroke="#f6d472" stroke-width="2"><circle cx="12" cy="12" r="10"/><path d="M7.5 12.5l3 3 6-6"/></svg><h4>Punctual, uniformed professional chauffeurs</h4><p>Our experienced chauffeurs arrive on time in pristine uniforms with white gloves</p></li>
        <li><svg width="14" height="14" viewBox="0 0 24 24" fill="none" stroke="#f6d472" stroke-width="2"><circle cx="12" cy="12" r="10"/><path d="M7.5 12.5l3 3 6-6"/></svg><h4>Exceptional comfort, safety, and style</h4><p>Fully insured, regularly maintained vehicles ensuring the highest standards</p></li>
        <li><svg width="14" height="14" viewBox="0 0 24 24" fill="none" stroke="#f6d472" stroke-width="2"><circle cx="12" cy="12" r="10"/><path d="M7.5 12.5l3 3 6-6"/></svg><h4>Available across Poland for weddings &amp; photo sessions</h4><p>Serving couples throughout Poland with flexible scheduling and locations</p></li>
      </ul>
      <div class="detail-photo" role="img" aria-label="Chauffeur opening the car door as the bride steps out">
        <span class="blob" style="left:-10px;top:-10px;width:60px;height:60px"></span>
        <span class="blob" style="right:-20px;bottom:-20px;width:90px;height:90px"></span>
        <span class="t1">Elegant Detail Shot</span>
        <span class="t2">Chauffeur opening door, bride stepping out</span>
      </div>
    </div>
  </div>
</section>

<section class="reviews">
  <div class="wrap">
    <h2>Words from Our <span class="gold">Happy Couples</span></h2>
    <div class="quotes">
      <blockquote class="quote">
        <div class="stars">
          <svg width="62" height="12" viewBox="0 0 62 12" fill="#f6d472"><path id="st" d="M6 0l1.8 3.9 4.2.4-3.2 2.8 1 4.1L6 9l-3.8 2.2 1-4.1L0 4.3l4.2-.4z"/><use href="#st" x="12.5"/><use href="#st" x="25"/><use href="#st" x="37.5"/><use href="#st" x="50"/></svg>
        </div>
        <p>"It felt like a dream. The car was stunning and the service was flawless."</p>
        <p class="who">– Ola &amp; Tomasz</p>
      </blockquote>
      <blockquote class="quote">
        <div class="stars"><svg width="62" height="12" viewBox="0 0 62 12" fill="#f6d472"><use href="#st"/><use href="#st" x="12.5"/><use href="#st" x="25"/><use href="#st" x="37.5"/><use href="#st" x="50"/></svg></div>
        <p>"Our guests were amazed. The car made our entrance unforgettable."</p>
        <p class="who">– Ewa &amp; Janusz</p>
      </blockquote>
      <blockquote class="quote">
        <div class="stars"><svg width="62" height="12" viewBox="0 0 62 12" fill="#f6d472"><use href="#st"/><use href="#st" x="12.5"/><use href="#st" x="25"/><use href="#st" x="37.5"/><use href="#st" x="50"/></svg></div>
        <p>"From start to finish, everything was elegant, smooth, and stress-free."</p>
        <p class="who">– Iga &amp; Marek</p>
      </blockquote>
    </div>
  </div>
</section>

<section class="cta">
  <h2>Your Dream Car Is <span class="gold">One Click Away</span></h2>
  <p class="sub">Reserve early to guarantee availability for your special day.</p>
  <a class="btn btn-gold" href="#contact">Contact Us Today</a>
  <div class="divider"><span></span><i></i><span></span></div>
</section>

<footer class="footer" id="contact">
  <div class="wrap">
    <div class="foot-cols">
      <div class="foot-brand">
        <div class="foot-name"><i></i>Velvet Route Weddings</div>
        <p>Creating unforgettable wedding moments with luxury vehicles and professional service. Your special day deserves nothing less than perfection.</p>
        <div class="socials"><i></i><i></i></div>
      </div>
      <div class="foot-col">
        <h5>Quick Links</h5>
        <ul><li>Home</li><li>Fleet</li><li>Services</li><li>Why Us</li><li>Contact</li><li>FAQ</li></ul>
      </div>
      <div class="foot-col contact">
        <h5>Contact</h5>
        <ul>
          <li><svg width="10" height="10" viewBox="0 0 24 24" fill="none" stroke="#f6d472" stroke-width="2"><rect x="3" y="5" width="18" height="14" rx="2"/><path d="M3 7l9 6 9-6"/></svg>info@velvetroute.pl</li>
          <li><svg width="10" height="10" viewBox="0 0 24 24" fill="none" stroke="#f6d472" stroke-width="2"><path d="M5 3h4l2 5-3 2a11 11 0 0 0 6 6l2-3 5 2v4a2 2 0 0 1-2 2A17 17 0 0 1 3 5a2 2 0 0 1 2-2z"/></svg>+48 500 210 340</li>
          <li><svg width="10" height="10" viewBox="0 0 24 24" fill="none" stroke="#f6d472" stroke-width="2"><circle cx="12" cy="12" r="9"/><path d="M12 7v5l3 2"/></svg>Mon-Sun: 8:00-20:00</li>
        </ul>
      </div>
    </div>
    <div class="foot-bottom"><span>© 2024 Velvet Route Weddings. All rights reserved.</span><span>English</span></div>
  </div>
</footer>

</body>
</html>
```